Communication and Marketing agency needs a new presentation card

We are a group of communication and marketing agencies specialized in companies that are in the logistics and industrial sector. The head agency is TELVANO Grupo and the group consists of 4 agencies: TELVANO Media, TELVANO Digital, TELVANO Research and DifundeEnPantalla. We hace 4 offices in Spain (Madrid, Barcelona, Valencia and Murcia). We are looking for a clean and attractive design that transmits our experience, brand presence in the market and knowledge to those who receive the card.It has to maintain the colors of the logo that is attached.
Target Market(s)
logistics and industrial sector
Marketing department
Contact Information for Business Card
Clean and attractive design

```html
<!DOCTYPE html>
<html lang="es">
<head>
<meta charset="utf-8">
<title>TELVANO Grupo – Tarjeta de presentación</title>
<link rel="stylesheet" href="https://fonts.googleapis.com/css2?family=Open+Sans:wght@400;600;700&display=swap">
<style>
  :root {
    --stage: #666666;
    --card: #ffffff;
    --brand-red: #b01c28;
    --ink: #333333;
    --muted: #9a9a9a;
    --shadow: rgba(0, 0, 0, 0.45);
  }
  * { margin: 0; padding: 0; box-sizing: border-box; }
  html, body { width: 1200px; height: 900px; overflow: hidden; }
  body {
    position: relative;
    background: var(--stage);
    font-family: "Open Sans", Arial, sans-serif;
  }
  .card {
    position: absolute;
    width: 478px;
    height: 295px;
    background: var(--card);
    box-shadow: 3px 4px 4px var(--shadow);
    overflow: hidden;
  }
  .card--front {
    left: 120px; top: 275px;
    border-radius: 0 60px 0 60px;
  }
  .card--back {
    left: 606px; top: 273px;
    border-radius: 60px 0 60px 0;
  }

  /* Front */
  .wordmark {
    position: absolute;
    font-weight: 600;
    color: var(--brand-red);
    line-height: 1;
    text-align: right;
  }
  .card--front .wordmark { left: 30px; top: 113px; width: 192px; }
  .wordmark__name { display: block; font-size: 36px; letter-spacing: 2px; }
  .wordmark__group { display: block; font-size: 22px; margin-top: 6px; }
  .divider {
    position: absolute;
    left: 249px; top: 93px;
    width: 1px; height: 106px;
    background: #c8c8c8;
  }
  .contact { position: absolute; left: 269px; top: 90px; }
  .contact__name {
    font-size: 16px; font-weight: 700;
    color: var(--brand-red); letter-spacing: 0.3px; line-height: 20px;
  }
  .contact__role { font-size: 14px; color: var(--ink); line-height: 18px; margin-bottom: 6px; }
  .contact__list { list-style: none; }
  .contact__item {
    display: flex; align-items: center;
    font-size: 14px; color: var(--ink); line-height: 17.5px;
  }
  .contact__icon { width: 10px; height: 10px; margin-right: 7px; fill: var(--brand-red); flex: none; }

  /* Back */
  .back__band {
    position: absolute; left: 0; top: 0;
    width: 100%; height: 227px;
    background: var(--brand-red);
  }
  .card--back .wordmark { color: #ffffff; left: 120px; top: 113px; width: 236px; }
  .card--back .wordmark__name { font-size: 40px; }
  .card--back .wordmark__group { font-size: 24px; }
  .agencies {
    position: absolute; left: 30px; top: 240px;
    width: 420px;
    display: flex; justify-content: space-between; align-items: flex-start;
  }
  .agency {
    font-weight: 600; font-size: 13px; line-height: 1.05;
    text-align: right; letter-spacing: 0.3px;
  }
  .agency span { display: block; font-size: 10px; }
  .agency--red { color: var(--brand-red); }
  .agency--grey { color: #555555; }
  .agency--pantalla { text-align: left; font-size: 13px; }
</style>
</head>
<body>

  <section class="card card--front" aria-label="Tarjeta, cara frontal">
    <div class="wordmark">
      <span class="wordmark__name">TELVANO</span>
      <span class="wordmark__group">Grupo</span>
    </div>
    <div class="divider"></div>
    <div class="contact">
      <p class="contact__name">MARCOS HERRERA</p>
      <p class="contact__role">Managing Director</p>
      <ul class="contact__list">
        <li class="contact__item">
          <svg class="contact__icon" viewBox="0 0 10 10" aria-hidden="true"><path d="M1 3.5C1 2 2.5 1.5 5 1.5S9 2 9 3.5L7.5 4 7 3H3L2.5 4ZM2.5 5h5l1 4h-7z"/></svg>
          044-987 654 321
        </li>
        <li class="contact__item">
          <svg class="contact__icon" viewBox="0 0 10 10" aria-hidden="true"><path d="M3 0h4a1 1 0 0 1 1 1v8a1 1 0 0 1-1 1H3a1 1 0 0 1-1-1V1a1 1 0 0 1 1-1zm0.5 1.2v6.3h3V1.2z"/></svg>
          044-987 654 321
        </li>
        <li class="contact__item">
          <svg class="contact__icon" viewBox="0 0 10 10" aria-hidden="true"><path d="M0 2h10v6H0zM0.8 2.6 5 5.6l4.2-3z" fill-rule="evenodd"/></svg>
          info@telvanogrupo.es
        </li>
        <li class="contact__item">
          <svg class="contact__icon" viewBox="0 0 10 10" aria-hidden="true"><circle cx="5" cy="5" r="4.6"/></svg>
          www.telvanogrupo.es
        </li>
      </ul>
    </div>
  </section>

  <section class="card card--back" aria-label="Tarjeta, cara posterior">
    <div class="back__band"></div>
    <div class="wordmark">
      <span class="wordmark__name">TELVANO</span>
      <span class="wordmark__group">Grupo</span>
    </div>
    <div class="agencies">
      <p class="agency agency--red">TELVANO<span>Media</span></p>
      <p class="agency agency--grey">TELVANO<span>Research</span></p>
      <p class="agency agency--grey">TELVANO<span>Digital</span></p>
      <p class="agency agency--red agency--pantalla">Difunde<br>EnPantalla</p>
    </div>
  </section>

</body>
</html>
```